RW Framewell Inc Business cards

We need business cards using our existing logo but slightly modified. Right now the logo says RW Loadbearing Masonry. We want to keep the RW part of the design, but replace the Structural Concrete portion with "FRAMEWELL". Please see the attached file.
Ideally this would be a blank template so we can add Different Names, titles, and phone numbers later.
On the one side we want only the logo and on the other side the detail. I'm attaching an example for you to see.
Please reach out with any other questions. Our address and other details will be given out once we find a design we like.

Target Market(s)

Construction Industry

```html
<!DOCTYPE html>
<html lang="en">
<head>
<meta charset="utf-8">
<title>RW Framewell Inc — Business Cards</title>
<link rel="stylesheet" href="https://fonts.googleapis.com/css2?family=Montserrat:wght@600&family=Roboto:wght@400;500;700&display=swap">
<style>
  :root {
    --page-bg: #3a3a3c;
    --card-black: #1c1c1d;
    --brand-blue: #2f64a8;
    --divider-grey: #7d7d7f;
    --logo-grey: #8a8a8c;
    --text-white: #ffffff;
  }
  * { box-sizing: border-box; margin: 0; padding: 0; }
  html, body {
    width: 799px;
    height: 1200px;
    overflow: hidden;
  }
  body {
    background: var(--page-bg);
    position: relative;
    font-family: "Roboto", Arial, sans-serif;
  }
  .card {
    position: absolute;
    left: 110px;
    width: 580px;
    height: 330px;
    border-radius: 4px;
    overflow: hidden;
    box-shadow: 0 10px 28px rgba(0, 0, 0, 0.45);
  }
  .card--front {
    top: 140px;
    background: var(--card-black);
  }
  .card--back {
    top: 700px;
    background: var(--brand-blue);
  }
  .wordmark {
    position: absolute;
    display: flex;
    align-items: center;
    gap: 14px;
    font-family: "Montserrat", Arial, sans-serif;
    font-weight: 600;
    text-transform: uppercase;
    letter-spacing: 0.16em;
    white-space: nowrap;
  }
  .wordmark__square {
    width: 22px;
    height: 22px;
    background: var(--brand-blue);
    flex: none;
  }
  .card--front .wordmark {
    left: 50%;
    top: 50%;
    transform: translate(-50%, -50%);
    font-size: 34px;
    color: var(--text-white);
  }
  .card--back .wordmark {
    left: 30px;
    top: 104px;
    font-size: 18px;
    line-height: 1.35;
    color: var(--logo-grey);
    gap: 10px;
    z-index: 1;
  }
  .card--back .wordmark__square {
    width: 14px;
    height: 14px;
  }
  .wordmark__line { display: block; }
  .back-shapes {
    position: absolute;
    inset: 0;
    width: 580px;
    height: 330px;
  }
  .back-shapes__divider { fill: var(--divider-grey); }
  .back-shapes__panel { fill: var(--card-black); }
  .contact {
    position: absolute;
    left: 318px;
    top: 74px;
    width: 250px;
    color: var(--text-white);
  }
  .contact__name {
    font-size: 22px;
    font-weight: 700;
    line-height: 1.1;
  }
  .contact__title {
    font-size: 14px;
    font-weight: 400;
    margin-top: 2px;
    margin-bottom: 16px;
  }
  .contact__list { list-style: none; }
  .contact__item {
    display: flex;
    align-items: center;
    gap: 10px;
    font-size: 14px;
    line-height: 22px;
  }
  .contact__icon {
    width: 13px;
    height: 13px;
    flex: none;
    fill: var(--text-white);
  }
  .contact__address {
    font-style: normal;
    font-size: 14px;
    line-height: 20px;
    margin-top: 6px;
    margin-left: -26px;
  }
</style>
</head>
<body>

  <section class="card card--front" aria-label="Card front">
    <div class="wordmark">
      <span class="wordmark__square"></span>
      <span class="wordmark__name">RW Framewell</span>
    </div>
  </section>

  <section class="card card--back" aria-label="Card back">
    <svg class="back-shapes" viewBox="0 0 580 330" aria-hidden="true">
      <path class="back-shapes__divider" d="M0 0 H296 C236 110 206 230 164 330 H0 Z"/>
      <path class="back-shapes__panel" d="M0 0 H282 C222 110 192 230 148 330 H0 Z"/>
    </svg>

    <div class="wordmark">
      <span class="wordmark__square"></span>
      <span class="wordmark__name">
        <span class="wordmark__line">RW</span>
        <span class="wordmark__line">Framewell</span>
      </span>
    </div>

    <div class="contact">
      <h1 class="contact__name">Daniel RW Harlow</h1>
      <p class="contact__title">Managing Director</p>
      <ul class="contact__list">
        <li class="contact__item">
          <svg class="contact__icon" viewBox="0 0 16 16" aria-hidden="true"><path d="M3 1 L6 1 L7 5 L5 6.5 C6 8.5 7.5 10 9.5 11 L11 9 L15 10 L15 13 C15 14 14 15 13 15 C6.5 14.5 1.5 9.5 1 3 C1 2 2 1 3 1 Z"/></svg>
          <span>555-010-2468</span>
        </li>
        <li class="contact__item">
          <svg class="contact__icon" viewBox="0 0 16 16" aria-hidden="true"><path d="M1 3 H15 V13 H1 Z M2 4 L8 9 L14 4 Z" fill-rule="evenodd"/></svg>
          <span>daniel@framewellbuild.com</span>
        </li>
        <li class="contact__item">
          <svg class="contact__icon" viewBox="0 0 16 16" aria-hidden="true"><path d="M8 1 A7 7 0 1 0 8.01 1 Z M8 2.5 A5.5 5.5 0 1 1 7.99 2.5 Z M2 7.3 H14 V8.7 H2 Z M7.3 2 H8.7 V14 H7.3 Z" fill-rule="evenodd"/></svg>
          <span>www.framewellbuild.com</span>
        </li>
      </ul>
      <address class="contact__address">418 Timberline Ave., Oakridge,<br>Oregon, US 97463</address>
    </div>
  </section>

</body>
</html>
```